Carpet cleaning company focused on high quality needs business cards

We are a growing company that just merged with another company and need to design a new business card. We do both residential as well as commercial cleaning. We do carpet, tile & grout, upholstery, hard floors, and stain & pet odor removal. We treat our customers like family and strive to achieve outstanding results with every job.

```html
<!DOCTYPE html>
<html lang="en">
<head>
<meta charset="utf-8">
<title>Kindred Steam Care – Business Cards</title>
<link rel="stylesheet" href="https://fonts.googleapis.com/css2?family=Open+Sans:wght@400;600;700;800&display=swap">
<style>
  :root {
    --stage: #dcdde0;
    --card-white: #ffffff;
    --brand-red: #e8463d;
    --brand-blue: #1a7bc4;
    --ink: #111111;
    --text-dark: #1c1c1c;
    --shadow: rgba(0, 0, 0, 0.28);
  }
  * { box-sizing: border-box; margin: 0; padding: 0; }
  html, body {
    width: 1200px; height: 780px; overflow: hidden;
    background: var(--stage);
    font-family: "Open Sans", Arial, sans-serif;
  }
  .stage {
    width: 1200px; height: 780px;
    display: flex; align-items: center; justify-content: center; gap: 40px;
  }
  .card {
    position: relative; width: 560px; height: 320px; overflow: hidden;
    box-shadow: 0 10px 24px var(--shadow);
  }

  /* ---------- Front ---------- */
  .card--front { background: var(--card-white); }
  .card__faint-art {
    position: absolute; left: 250px; top: 20px; width: 200px; height: 200px;
    border-radius: 50%;
    background: radial-gradient(circle, rgba(26,123,196,0.07), rgba(232,70,61,0.03) 60%, transparent 72%);
  }
  .card__corner-tab {
    position: absolute; right: 0; top: 0; width: 22px; height: 46px;
    background: var(--brand-blue);
  }
  .brand-art {
    position: absolute; left: 24px; top: 70px; width: 130px; height: 115px;
    background: linear-gradient(135deg, var(--brand-blue) 0%, #c9a060 50%, var(--brand-red) 100%);
  }
  .brand-name {
    position: absolute; left: 166px; top: 74px; width: 170px;
    font-weight: 800; font-size: 30px; line-height: 1.02; color: var(--ink);
  }
  .person { position: absolute; right: 34px; top: 40px; text-align: right; }
  .person__name { font-size: 30px; font-weight: 700; letter-spacing: 0.5px; line-height: 1.1; }
  .person__first { color: var(--brand-blue); }
  .person__last { color: var(--brand-red); }
  .person__title { font-size: 15px; font-weight: 600; color: var(--text-dark); letter-spacing: 0.5px; }
  .person__rule {
    margin-top: 6px; margin-left: auto; width: 200px; height: 1.5px; background: var(--brand-red);
  }
  .divider {
    position: absolute; left: 40px; top: 198px; width: 520px; height: 1.5px; background: var(--brand-red);
  }
  .contact { position: absolute; left: 40px; top: 210px; list-style: none; }
  .contact__item {
    display: flex; align-items: center; gap: 10px;
    font-size: 15px; color: var(--text-dark); line-height: 24px;
  }
  .contact__icon { width: 14px; height: 14px; flex: none; }
  .address {
    position: absolute; right: 34px; top: 214px; text-align: right;
    font-size: 14px; line-height: 21px; color: var(--text-dark); letter-spacing: 0.3px;
  }
  .card__band { position: absolute; left: 0; bottom: 0; width: 560px; height: 60px; }

  /* ---------- Back ---------- */
  .card--back { background: var(--brand-red); }
  .back-art {
    position: absolute; left: 70px; top: 62px; width: 170px; height: 150px;
    background: linear-gradient(160deg, #ffffff 0%, #e6eef6 45%, #c9a060 100%);
  }
  .back-brand {
    position: absolute; left: 258px; top: 80px; width: 260px;
    font-weight: 800; font-size: 40px; line-height: 1.02; color: var(--ink);
  }
  .services { position: absolute; left: 0; top: 226px; width: 560px; text-align: center; color: #fff; }
  .services__heading {
    display: flex; align-items: center; justify-content: center; gap: 10px;
    font-size: 13px; font-weight: 700; letter-spacing: 0.6px;
  }
  .services__heading::before, .services__heading::after {
    content: ""; width: 130px; height: 1.5px; background: #fff;
  }
  .services__line { font-size: 13.5px; font-weight: 600; line-height: 22px; margin-top: 4px; }
  .services__line + .services__line { margin-top: 0; }
</style>
</head>
<body>
<main class="stage">

  <section class="card card--front" aria-label="Business card front">
    <div class="card__faint-art" role="img" aria-label="Faint mascot illustration in the background"></div>
    <div class="card__corner-tab"></div>

    <div class="brand-art" role="img" aria-label="Company mascot illustration: cleaner holding a steam wand on a red square"></div>
    <div class="brand-name">Kindred Steam Care</div>

    <div class="person">
      <p class="person__name"><span class="person__first">Lena</span> <span class="person__last">Marsh</span></p>
      <p class="person__title">Managing Director</p>
      <div class="person__rule"></div>
    </div>

    <div class="divider"></div>

    <ul class="contact">
      <li class="contact__item">
        <svg class="contact__icon" viewBox="0 0 16 16" aria-hidden="true"><path d="M4 1l3 3-2 2c1 2 3 4 5 5l2-2 3 3-2 2C7 14 2 9 2 3z" fill="var(--brand-blue)"/></svg>
        (555) 014-2290
      </li>
      <li class="contact__item">
        <svg class="contact__icon" viewBox="0 0 16 16" aria-hidden="true"><rect x="1" y="3" width="14" height="10" rx="1" fill="var(--brand-blue)"/><path d="M1 4l7 5 7-5" stroke="#fff" stroke-width="1.4" fill="none"/></svg>
        hello@kindredsteam.com
      </li>
      <li class="contact__item">
        <svg class="contact__icon" viewBox="0 0 16 16" aria-hidden="true"><circle cx="8" cy="8" r="7" fill="var(--brand-blue)"/><path d="M1 8h14M8 1c-3 4-3 10 0 14M8 1c3 4 3 10 0 14" stroke="#fff" stroke-width="1" fill="none"/></svg>
        www.kindredsteam.com
      </li>
    </ul>

    <address class="address" style="font-style:normal">
      418 Meadowlark Ave. Suite 120<br>
      Riverton, TX 75001
    </address>

    <svg class="card__band" viewBox="0 0 560 60" aria-hidden="true">
      <path d="M0 42 H300 Q306 42 308 36 L312 24 Q314 18 320 18 H560 V60 H0 Z" fill="var(--brand-blue)"/>
      <path d="M0 48 H300 Q310 48 313 40 L316 32 Q318 26 326 26 H560 V60 H0 Z" fill="var(--brand-red)"/>
    </svg>
  </section>

  <section class="card card--back" aria-label="Business card back">
    <div class="back-art" role="img" aria-label="Company mascot illustration: cleaner holding a steam wand on a white panel"></div>
    <div class="back-brand">Kindred Steam Care</div>

    <div class="services">
      <p class="services__heading">OUR SERVICES</p>
      <p class="services__line">● Both residential as well as commercial cleaning</p>
      <p class="services__line">● Carpet ● Tile &amp; grout ● Upholstery ● Hard floors ● Stain &amp; pet odor removal</p>
    </div>
  </section>

</main>
</body>
</html>
```